Verpackungen für Shampoos
Zielgruppe
Wir sind ein kleines Familienunternehmen mit 2-3 Friseurfilialen und Onlineshop im Naturfriseurbereich, arbeiten mit ökologischen, nachhaltigen und natürlichen Produkten und vertreiben unsere eigene Haarbürste. Wir betreiben mit Sol Verde unsere eigene Marke in diesem Bereich. Erste Produkte, wie eine eigene Haarbürste sind bereits vorhanden und entstanden.
Für unsere erste Shampoo Serie suchen wir ein klares, cleanes und hochwertiges Design. Die 200ml Shampooflasche kommt komplett in weiß und besteh aus recyceltem Material. Es soll klar die ökologisch nachhaltige und etwas höherpreisige Marke kommuniziert werden. Dabei sehen wir vom Stil „weniger ist mehr“ als ganz klare Designvorgabe. Anbei auch ein Beispiel von Pavura, die das ganze sehr schön umgesetzt haben.
Die INCI sind noch nicht final. Es wäre schön, wenn hier ein Platzhalter eingefügt würde. Da eine der Hauptzielgruppen auch Österreicher sind, würden wir uns über ein kleines „Made in Austria“ auf der Vorderseite (evtl. ganz unten auf der Flasche) freuen.
Insgesamt sind es vier verschiedene Shampoos, die aus der gleichen Serie stammen. Es wäre schön, wenn man diese auch direkt unterscheiden könnte. Vielleicht durch ein grafisches Element, oder einfach nur durch die verschiedenen Namenserweiterungen. Hier die Aufstellung mit den Erweiterungen:
Es werden 4 verschiedene Shampoos, die Namen sind:
Change - Strapaziertes Haar
Care - Normales Haar
Sensitiv - Empfindliche Kopfhaut
Balancing - Fettiges Haar
Zielgruppe:
Weiblich, 30-60 Jahre, mittleres bis gehobenes Einkommen, nachhaltig, ökologisch, natürlich, legt Wert auf hochwertige Produkte und Dienstleistungen, achtet auf Konsum.
Aufgabenstellung
Die Landingpage zur Bürste ist hier erreichbar (Beispiel):
Vielleicht hilft das etwas um das Design und die Tonality aufzuschnappen: https://sol-verde.de/gold-birch-wildschweinborstenbuerste/
Es wäre super, wenn das Design der Flasche ähnlich klar und strukturiert ist.
Die Shampoos sind komplett vegan und made in Austria. Die beiden Aspekte sollten in Design auch aufgegriffen werden. Da wir einen 4 farbigen Tamponade/Siebdruck auf der Flasche anwenden, stehen leider nicht so viele Farben zur Verfügung (3-4).
Link zur Flasche:
https://www.brumoxa.com/de/kosmetik/varleno/varleno-tubica/flasche-heavy-200ml-24-410-plastik
Des Weiteren kann sich noch am Sol Verde Haarkonzept und unserem Dienstleistungsflyer orientiert werden.
Benefits:
-       Pflegt das Haar, hält es geschmeidig
- Bio Shampoo Konzentrat
-       Die Grundlage für gesunde Kopfhaut und schönes Haar*
-       Vermindert Spliss*
-       Hält die Haare natürlich geschmeidig
-       Regt die Durchblutung der Kopfhaut an
-       Verteilt Nährstoffe von der Wurzel bis in die Spitzen*
-       Verbessert das Kopfhautklima*
-       Für eine gut durchblutete und gesunde Kopfhaut mit glänzenden und
geschmeidigen Haaren*
-       Entfernt Schuppen und abgestorbene Hautpartikel
-       Verbessert natürlich die allgemeine Haarstruktur
-       Entwirrt langes und gelocktes Haar
-       Reinigt die Kopfhaut ohne Chemie*
-       Mehr Volumen im Haar
-       Mehr Stand im Haar durch Kräftigung der Haarbalkmuskulatur
-       Spart Shampoo und hilft Shampoo seltener und weniger zu nutzen
-       Nährstoffversorgung bis in die Haarspitzen
Inhaltsstoffe:
Care
Aloe Vera Direktsaft*, Decyl Glucoside, Coco Glucoside, Lauryl Glucoside, Hopfenextrakt*, Pentylene Glycol green, Meli..

```html
<!DOCTYPE html>
<html lang="de">
<head>
<meta charset="utf-8">
<title>Sol Verde – Shampoo Sensitiv</title>
<link href="https://fonts.googleapis.com/css2?family=Montserrat:wght@400;500;700&display=swap" rel="stylesheet">
<style>
  :root {
    --backdrop: #e4e4e4;
    --bottle: #fbfbfb;
    --cap: #ededed;
    --accent-gold: #cf9337;
    --ink: #1e1e1e;
    --ink-soft: #3a3a3a;
  }
  * { margin: 0; padding: 0; box-sizing: border-box; }
  html, body { width: 1200px; height: 1200px; overflow: hidden; }
  body {
    background: var(--backdrop);
    font-family: "Montserrat", Arial, sans-serif;
    position: relative;
  }
  .bottle { position: absolute; }
  .bottle__cap {
    position: absolute;
    background: var(--cap);
    border-radius: 6px 6px 0 0;
  }
  .bottle__stripe {
    position: absolute;
    top: 0; bottom: 0;
    background: var(--accent-gold);
  }
  .bottle__body {
    position: absolute;
    background: var(--bottle);
    border-radius: 4px;
  }
  .brand-name {
    position: absolute;
    left: 0; right: 0;
    text-align: center;
    color: var(--ink-soft);
    font-weight: 400;
    white-space: nowrap;
  }

  /* back of bottle */
  .bottle--back .bottle__cap { left: 342px; top: 100px; width: 131px; height: 144px; }
  .bottle--back .bottle__stripe { left: 67px; width: 27px; }
  .bottle--back .bottle__body { left: 293px; top: 244px; width: 227px; height: 809px; }
  .bottle--back .brand-name { top: 638px; font-size: 7px; }
  .ingredients {
    position: absolute;
    left: 6px; right: 6px;
    top: 670px;
    text-align: center;
    color: var(--ink-soft);
    font-size: 8.4px;
    line-height: 12.2px;
    white-space: nowrap;
  }
  .ingredients__title { margin-bottom: 20px; }

  /* front of bottle */
  .bottle--front .bottle__cap { left: 618px; top: 162px; width: 131px; height: 147px; }
  .bottle--front .bottle__stripe { left: 35px; width: 58px; }
  .bottle--front .bottle__body { left: 569px; top: 309px; width: 227px; height: 809px; }
  .bottle--front .brand-name { top: 290px; font-size: 21px; }
  .product-name {
    position: absolute;
    left: 0; right: 0;
    top: 462px;
    text-align: center;
    color: var(--ink);
    font-weight: 700;
    font-size: 11.5px;
    line-height: 1.45;
    letter-spacing: 0.02em;
  }
  .seal {
    position: absolute;
    left: 82px; top: 598px;
  }
  .origin {
    position: absolute;
    left: 0; right: 0;
    top: 721px;
    text-align: center;
    color: var(--ink);
    font-weight: 500;
    font-size: 7.5px;
    letter-spacing: 0.18em;
  }
</style>
</head>
<body>

<div class="bottle bottle--back">
  <div class="bottle__cap"><div class="bottle__stripe"></div></div>
  <div class="bottle__body">
    <p class="brand-name">Sol Verde</p>
    <div class="ingredients">
      <p class="ingredients__title">Inhaltsstoffe:</p>
      <p>Care<br>
      Aloe Vera Direktsaft*, Decyl Glucoside,<br>
      Coco Glucoside, Lauryl Glucoside, Hopfenextrakt*,<br>
      Pentylene Glycol green, Melissenblätter-Extrakt*,<br>
      Arganöl*, Brokkolisamenöl*, Xanthan Gum,<br>
      Parfümöl natürlich ‘Maiglöckchen’</p>
    </div>
  </div>
</div>

<div class="bottle bottle--front">
  <div class="bottle__cap"><div class="bottle__stripe"></div></div>
  <div class="bottle__body">
    <p class="brand-name">Sol Verde</p>
    <p class="product-name">SENSITIV<br>EMPFINDLICHE KOPFHAUT</p>
    <svg class="seal" width="64" height="64" viewBox="0 0 64 64" aria-hidden="true">
      <circle cx="32" cy="32" r="29" fill="none" stroke="var(--ink)" stroke-width="1.2"/>
    </svg>
    <p class="origin">MADE IN AUSTRIA</p>
  </div>
</div>

</body>
</html>
```